Webdesign für freie Trauungen
Zielgruppe
Webseite für Hochzeitspaare, Trauerende, Bestatter, Interessierte
Aufgabenstellung
Internetseite
Briefing:
Onepager
Internetseite soll wirken:
Modern
Schlank
Klar
Vertrauenserweckend
professionell
Home:
Reden für besondere Momente im Leben
Schrift an Flyer anpassen
REDEN.
ERZÄHLEN.
ERINNERN.
BERÜHREN.
Bild von mir,
Dazu, meine Reden sind:
freundlich
authentisch
ehrlich
einfühlsam
taktvoll
humorvoll
tiefsinnig
tröstend
nett
zugewandt
interessant
nach Euren Wünschen
mit Euren Inhalten
individuell
sehr persönlich
kreativ
wortgewandt
erfahren
Sprechen Sie mich an! ?
FREIE TRAUUNG:
EINFACH HIMMLISCH!
eine Liebesgeschichte erzählen
Sich ein Versprechen geben
JA zueinander sagen
Mit lieben Menschen feiern
wo, wann, wie - das entscheidet Ihr!
Segensfeier - Willkommensfeier:
im Leben willkommen heißen
Was bedeutet der Name des Kindes?
Was wollt Ihr Eurem Kind mitgeben?
Was wünscht Ihr Euch für Euer Kind?
TRAUERFEIER:
an schöne Momente erinnern
Einen Menschen mit Worten lebendig werden lassen
Mit einer persönlichen und bewegenden Ansprache
Mit all dem, was Sie sich wünschen!
REDEN ZU GEBURTSTAGEN:
mit Humor, Witz und Verstand gemeinsam zurück schauen
Und von Träumen und Sehnsüchten erzählen
Reden zum Jubiläum:
gemeinsam zurück schauen
Geleistetes würdigen
Veränderungen verständlich machen
Ausblicke wagen
Biographien:
festhalten, damit nichts von Ihrer Lebensgeschichte verloren geht
Sie erinnern sich und ich schreibe auf
Referenzen:
???? Wie am besten ???
Persönliches Vita:
Studium an der Hohen Akademie Tellbrück:
- Publizistik
Germanistik
Volkswirtschaftslehre
Lateinamerikanistik
Abschluß: Magistra Artium
Freie Rednerin seit 1998
Telefonnummer 015923847261
Email: marlies.Kersten@postfeld.de
Wirk..

```html
<!DOCTYPE html>
<html lang="de">
<head>
<meta charset="utf-8">
<title>Kersten Reden – Reden für besondere Momente</title>
<link href="https://fonts.googleapis.com/css2?family=Signika:wght@300;400;600&family=Open+Sans:wght@300;400;600;700&display=swap" rel="stylesheet">
<style>
:root{
  --teal:#5b9591;
  --teal-dark:#4f8581;
  --text:#666a6c;
  --dark:#4b4c4d;
  --light-bg:#f8f8f8;
  --line:#d5d8d8;
}
*{box-sizing:border-box;margin:0;padding:0}
html,body{width:1200px;height:4322px;overflow:hidden}
body{font-family:"Open Sans",sans-serif;font-weight:300;color:var(--text);background:#fff;position:relative}
.abs{position:absolute}
h2{font-family:"Signika",sans-serif;font-weight:600;color:var(--teal)}
.photo{position:absolute}
.btn{position:absolute;display:flex;align-items:center;justify-content:center;font-size:13px;font-weight:400;color:#fff;background:var(--teal)}

/* Navigation */
.nav{position:absolute;top:0;left:0;width:1200px;height:65px;background:#fff}
.brand{position:absolute;left:252px;top:18px;font-weight:400;font-size:19px;color:#333;letter-spacing:.5px}
.nav-links{position:absolute;top:24px;left:530px;display:flex;font-size:12.5px;font-weight:400;color:#666}
.nav-links span{padding:0 12px;position:relative}
.nav-links .active{color:var(--teal)}
.nav-links .active:after{content:"";position:absolute;left:0;right:0;bottom:-12px;height:2px;background:var(--teal)}

/* Hero */
.hero{position:absolute;top:65px;left:0;width:1200px;height:579px;background:linear-gradient(90deg,#868a8b 0%,#7b7f81 50%,#868889 100%)}
.hero-portrait{left:150px;top:0;width:420px;height:579px;background:linear-gradient(180deg,#d9c89c 0%,#a39a8c 45%,#efece6 75%,#8d8579 100%);opacity:.85}
.hero-hello{left:609px;top:196px;font-family:"Signika",sans-serif;font-size:27px;color:#fff;font-weight:300}
.hero-name{left:609px;top:237px;font-family:"Signika",sans-serif;font-size:28px;color:#fff;font-weight:600}
.hero-lead{left:609px;top:297px;width:330px;font-size:12.5px;line-height:16px;color:#fff;font-weight:400}
.hero-box{left:609px;top:435px;width:168px;height:144px;border:1.5px solid #fff;border-bottom:none;padding:22px 0 0 16px;font-size:18px;line-height:28px;color:#fff;letter-spacing:1px;font-weight:400}

/* Leistungen */
.services{position:absolute;top:644px;left:0;width:1200px;height:287px;background:var(--light-bg)}
.services h2{position:absolute;left:253px;top:36px;font-size:25px;color:#4a4a4a}
.services p{position:absolute;left:253px;top:83px;width:145px;font-size:12px;line-height:16.5px}
.service-tile{position:absolute;top:44px;width:153px}
.service-tile .photo{position:relative;width:153px;height:153px}
.service-tile .num{position:absolute;left:-14px;top:118px;font-family:"Signika",sans-serif;font-size:48px;font-weight:600;color:#d7e4e3}
.service-tile .cap{margin-top:28px;text-align:center;font-size:12px;line-height:17px;color:#555;font-weight:400}

/* Feature rows */
.feature{position:absolute;left:0;width:1200px}
.feature h2{position:absolute;font-size:26px}
.feature .list{position:absolute;font-size:13px;line-height:25.3px}
.feature .small{position:absolute;font-size:13px;line-height:17px}
.strong-cap{position:absolute;font-size:12.5px;font-weight:700;color:#444}
.teal-note{position:absolute;font-size:13px;font-weight:700;color:var(--teal)}

/* Vita */
.vita{position:absolute;top:2269px;left:0;width:1200px;height:493px;border-bottom:1px solid #eee}
.vita-photo{left:250px;top:52px;width:349px;height:330px;background:linear-gradient(180deg,#8d9a8a 0%,#c9cfc6 45%,#7f7b73 100%)}
.vita-caption{position:absolute;left:250px;top:382px;width:349px;height:42px;background:#5a5d60;color:#fff;font-size:15px;font-weight:400;display:flex;align-items:center;justify-content:center}
.vita h2{position:absolute;left:638px;top:110px;font-size:27px}
.vita .study{position:absolute;left:638px;top:170px;font-size:12.5px;color:#444;font-weight:400}
.vita ul{position:absolute;left:638px;top:202px;list-style:none;font-size:11.5px;line-height:19px}
.vita ul li:before{content:"• "}
.vita .grad{position:absolute;left:638px;top:285px;font-size:12.5px;font-weight:600;color:#444}
.vita .degree{position:absolute;left:638px;top:317px;font-size:11px;color:var(--teal)}
.vita .since{position:absolute;left:638px;top:345px;font-size:12.5px;color:#444;font-weight:400}

/* Referenzen */
.refs h2{position:absolute;top:2810px;left:0;width:1200px;text-align:center;font-size:26px}
.ref-main{position:absolute;left:263px;top:2883px;width:452px;height:463px;background:var(--teal);color:#fff;padding:16px;font-size:10.6px;line-height:18px;font-weight:400}
.ref-main p{margin-bottom:16px}
.ref-card{position:absolute;left:738px;width:198px;background:#fff;box-shadow:0 0 6px rgba(0,0,0,.12);padding:14px 16px;font-size:10.5px;line-height:17.5px;color:#555;font-weight:400}
.ref-card p{margin-bottom:15px}
.ref-card b{font-weight:700;color:var(--teal-dark)}

/* About band */
.about{position:absolute;top:3447px;left:0;width:1200px;height:308px;background:var(--teal);color:#fff}
.about h2{position:absolute;left:250px;top:38px;font-size:26px;color:#fff}
.about .lead{position:absolute;left:250px;top:100px;width:700px;font-size:14.5px;line-height:17px;font-weight:700}
.about .body{position:absolute;left:250px;top:145px;width:700px;font-size:12px;line-height:17px;font-weight:400}
.signature{left:252px;top:194px;width:246px;height:72px;background:linear-gradient(90deg,rgba(255,255,255,.18),rgba(255,255,255,.05));border-radius:4px}
.social{position:absolute;top:215px;width:28px;height:28px;border-radius:50%}

/* Kontakt */
.contact h2{position:absolute;top:3822px;font-size:26px}
.contact .intro{position:absolute;left:257px;top:3886px;width:265px;font-size:13px;line-height:16.5px}
.contact .item{position:absolute;left:257px;font-size:13px;line-height:16px;display:flex;gap:8px}
.contact .item svg{flex:none;margin-top:3px}
.field{position:absolute;left:540px;width:403px;border:1px solid #c9cdcd;background:#fff;font-size:12px;color:#999;padding:7px 10px;font-weight:400}
.send{position:absolute;left:540px;top:4039px;width:403px;height:28px;background:var(--teal);color:#fff;font-size:13px;display:flex;align-items:center;justify-content:center;font-weight:400}

/* Footer */
.footer{position:absolute;left:0;top:4100px;width:1200px;height:222px}
.footer-brand{position:absolute;left:252px;top:145px;font-size:17px;color:#fff;font-weight:400;letter-spacing:.5px}
.footer-copy{position:absolute;left:456px;top:152px;font-size:11.5px;color:#fff;font-weight:400}
.footer-legal{position:absolute;left:819px;top:152px;font-size:11.5px;color:#fff;font-weight:400}
</style>
</head>
<body>

<header class="nav">
  <div class="brand">Kersten Reden</div>
  <nav class="nav-links">
    <span class="active">Start</span>
    <span>Leistungen ▾</span>
    <span>Persönliches Vita</span>
    <span>Referenzen</span>
    <span>Kontakt</span>
  </nav>
</header>

<section class="hero" role="img" aria-label="Porträtfoto der Rednerin Marlies Kersten vor grauer Wand">
  <div class="photo hero-portrait" role="img" aria-label="Porträt der Rednerin im beigen Blazer"></div>
  <div class="abs hero-hello">Herzlich Willkommen!</div>
  <div class="abs hero-name">Ich bin Marlies Kersten</div>
  <p class="abs hero-lead">ANSPRACHEN UND ZEREMONIEN für freie Trauungen, für Geburtstage, zu den Wendepunkten des Lebens und zum Abschied</p>
  <div class="btn" style="left:609px;top:366px;width:108px;height:31px">Leistungen</div>
  <div class="btn" style="left:740px;top:366px;width:87px;height:31px;background:#fff;color:#888">Kontakt</div>
  <div class="abs hero-box">REDEN.<br>ERZÄHLEN.<br>ERINNERN.<br>BERÜHREN.</div>
</section>

<section class="services">
  <h2>Leistungen</h2>
  <p>Muster Text Lorem ipsum dolor sit amet, consetetur sadipscing elitr, sed diam nonumy eirmod tempor invidunt ut labore.</p>
  <div class="service-tile" style="left:435px">
    <div class="photo" role="img" aria-label="Foto der Rednerin für Trau- und Geburtstagsreden" style="background:linear-gradient(160deg,#a9b49c,#e2d3a8 50%,#3d3f45)"></div>
    <div class="num">1</div>
    <div class="cap">Trau- &amp; Hochzeitsreden /<br>Reden zu Geburtstagen</div>
  </div>
  <div class="service-tile" style="left:612px">
    <div class="photo" role="img" aria-label="Foto der Rednerin mit Spiegelung in Glasfläche" style="background:linear-gradient(90deg,#6f7068,#cdbf98 35%,#4a4b4f 50%,#d8c89d 70%,#3a3b3e)"></div>
    <div class="num">2</div>
    <div class="cap">Trauerreden</div>
  </div>
  <div class="service-tile" style="left:790px">
    <div class="photo" role="img" aria-label="Foto der Rednerin mit Brille vor grünem Sessel" style="background:linear-gradient(120deg,#2f5c4e,#e4d6b0 45%,#c9b98f 70%,#2b4d42)"></div>
    <div class="num">3</div>
    <div class="cap">Reden zum Jubiläum /<br>Biographien</div>
  </div>
</section>

<section class="feature" style="top:931px;height:512px">
  <h2 style="left:72px;top:58px">Trau- &amp; Hochzeitsreden</h2>
  <div class="strong-cap" style="left:72px;top:118px">EINFACH HIMMLISCH!</div>
  <div class="list" style="left:72px;top:139px">eine Liebesgeschichte erzählen<br>Sich ein Versprechen geben<br>JA zueinander sagen<br>Mit lieben Menschen feiern</div>
  <div class="teal-note" style="left:72px;top:255px">wo, wann, wie – das entscheidet Ihr!</div>
  <h2 style="left:72px;top:300px">Reden zu Geburtstagen</h2>
  <div class="small" style="left:72px;top:356px">mit Humor, Witz und Verstand gemeinsam zurück schauen<br>Und von Träumen und Sehnsüchten erzählen</div>
  <div class="btn" style="left:72px;top:416px;width:129px;height:32px">Jetzt anfragen</div>
  <div class="photo" role="img" aria-label="Porträtfoto der Rednerin im Freien" style="left:601px;top:0;width:599px;height:512px;background:radial-gradient(ellipse at 50% 45%,#e9dcb8 0%,#cfc29c 35%,#9fae97 65%,#bfc9b8 100%)"></div>
</section>

<section class="feature" style="top:1443px;height:396px">
  <div class="photo" role="img" aria-label="Foto der Rednerin in Lederjacke mit Spiegelung" style="left:0;top:0;width:600px;height:396px;background:linear-gradient(90deg,#7b7c72,#d2c49e 25%,#505156 50%,#dacb9f 72%,#3a3b3f)"></div>
  <h2 style="left:671px;top:60px">Trauerreden</h2>
  <div class="list" style="left:671px;top:113px">an schöne Momente erinnern<br>Einen Menschen mit Worten lebendig werden lassen<br>Mit einer persönlichen und bewegenden Ansprache<br>Mit all dem, was Sie sich wünschen!</div>
  <div class="small" style="left:671px;top:225px;width:490px">Muster Text Lorem ipsum dolor sit amet, consetetur sadipscing elitr, sed diam nonumy eirmod tempor invidunt ut labore et dolore magna aliquyam erat, sed diam voluptua.</div>
  <div class="btn" style="left:671px;top:302px;width:130px;height:31px">Jetzt anfragen</div>
</section>

<section class="feature" style="top:1839px;height:430px">
  <h2 style="left:72px;top:60px">Reden zum Jubiläum</h2>
  <div class="list" style="left:72px;top:113px">gemeinsam zurück schauen<br>Geleistetes würdigen<br>Veränderungen verständlich machen<br>Ausblicke wagen</div>
  <h2 style="left:72px;top:223px">Biographien:</h2>
  <div class="small" style="left:72px;top:277px">festhalten, damit nichts von Ihrer Lebensgeschichte verloren geht.<br>Sie erinnern sich und ich schreibe auf</div>
  <div class="btn" style="left:72px;top:337px;width:129px;height:31px">Jetzt anfragen</div>
  <div class="photo" role="img" aria-label="Porträtfoto der Rednerin mit Brille auf grünem Samtsessel" style="left:601px;top:0;width:599px;height:430px;background:linear-gradient(110deg,#2c574a 0%,#3f6b5c 25%,#e6d8b3 50%,#cdbd93 70%,#2f5a4c 100%)"></div>
</section>

<section class="vita">
  <div class="photo vita-photo" role="img" aria-label="Foto der Rednerin am Rednerpult bei einer Zeremonie"></div>
  <div class="vita-caption">Marlies Kersten</div>
  <h2>Persönliches Vita</h2>
  <div class="study">Studium an der Hohen Akademie Tellbrück:</div>
  <ul>
    <li>Publizistik</li>
    <li>Germanistik</li>
    <li>Volkswirtschaftslehre</li>
    <li>Lateinamerikanistik</li>
  </ul>
  <div class="grad">Abschluß:</div>
  <div class="degree">Magistra Artium</div>
  <div class="since">Freie Rednerin seit 1998</div>
</section>

<section class="refs">
  <h2>Refenzen</h2>
  <div class="ref-main">
    <p><b>Unsere Trauer um Ehemann und Vater R.M.</b></p>
    <p>Liebe Frau Kersten,</p>
    <p>tiefsten Dank für Ihre sehr empathische und pietätvolle Begleitung im stilvollen Rahmen am 7. März 2019 — sie hat uns tröstend die Hand gereicht und uns gut getan. Ihre treffenden Worte zur „Lieblingsmusik“ und passende Zitate haben in Dankbarkeit viele Erinnerungen in uns wachgerufen. Der große Schmerz über seinen plötzlichen Verlust tut weh, aber es gibt auch Freude und Dankbarkeit für die mit ihm verbrachte schöne Lebenszeit.</p>
    <p>Sicherlich hätte sich mein geliebter Mann und unser geliebter Vater selber seinen „Zwangsabschied“ von uns allen nicht anders gewünscht. Nur wohl nicht zu diesem frühen Zeitpunkt.</p>
    <p>Großes Lob und Respekt für Ihre menschliche Dienstleistung! Sie haben es geschafft, dass wir diesen Tag in besonderer Erinnerung behalten dürfen – Sie sind ein Teil davon geworden und wir freuen uns, dass es Menschen wie Sie gibt!</p>
    <p>Mit herzlichem Dank wünschen wir Ihnen viel Kraft und weiterhin ein erfolgreiches Engagement bei Ihrem Schaffen — egal zu welchem Ereignis.</p>
    <p>Herzliche Grüße</p>
  </div>
  <div class="ref-card" style="top:2883px;height:297px">
    <p>Hallo Marlies,</p>
    <p>Die Familie Hollberg (Sterbefall Hollberg) hat mehr als Lob über dich ausgesprochen... Zitat "... nicht nur das die Rede in der Kapelle mega toll war, was auch die anderen gesagt haben, sondern die war ja beim Anruf und der Besprechung wie eine Seelsorgerin... die hat mir sehr geholfen..."</p>
    <p><b>LG Helga</b></p>
  </div>
  <div class="ref-card" style="top:3214px;height:132px">
    <p>Liebe Frau Kersten</p>
    <p>Vielen Dank für Ihre tolle Rede!</p>
    <p><b>Familie Ansorge</b></p>
  </div>
</section>

<section class="about">
  <h2>Muster über mich Text</h2>
  <p class="lead">Muster Text Lorem ipsum dolor sit amet, consetetur sadipscing elitr, sed diam nonumy eirmod tempor invidunt ut labore et dolore magna aliquyam erat, sed diam voluptua.</p>
  <p class="body">Lorem ipsum dolor sit amet, consetetur sadipscing elitr, sed diam nonumy eirmod tempor invidunt ut labore et dolore magna aliquyam erat, sed diam voluptua.</p>
  <div class="photo signature" role="img" aria-label="Handschriftliche Unterschrift von Marlies Kersten"></div>
  <span class="social" style="left:511px;background:#3b3f44" role="img" aria-label="Soziales Netzwerk 1"></span>
  <span class="social" style="left:552px;background:#3b3f44" role="img" aria-label="Soziales Netzwerk 2"></span>
  <span class="social" style="left:592px;background:#3b3f44" role="img" aria-label="Soziales Netzwerk 3"></span>
  <span class="social" style="left:634px;background:#3b3f44" role="img" aria-label="Soziales Netzwerk 4"></span>
</section>

<section class="contact">
  <h2 style="left:257px">Kontaktdaten</h2>
  <h2 style="left:540px">Kontaktformular</h2>
  <p class="intro">Sprechen Sie mich an und vereinbaren Sie einen unverbindlichen Termin mit mir. Ich freue mich auf Sie.</p>
  <div class="item" style="top:3962px">
    <svg width="9" height="11" viewBox="0 0 9 11"><rect x="1" y="0.5" width="7" height="10" rx="1.2" fill="none" stroke="#5b9591" stroke-width="1.2"/><circle cx="4.5" cy="8.5" r=".8" fill="#5b9591"/></svg>
    <span>015923847261</span>
  </div>
  <div class="item" style="top:3986px">
    <svg width="10" height="8" viewBox="0 0 10 8"><rect x="0.5" y="0.5" width="9" height="7" fill="#5b9591"/><path d="M0.5 0.5 5 4.5 9.5 0.5" fill="none" stroke="#fff" stroke-width="1"/></svg>
    <span>marlies.Kersten@postfeld.de</span>
  </div>
  <div class="item" style="top:4010px;width:260px">
    <svg width="10" height="12" viewBox="0 0 10 12" style="margin-top:18px"><path d="M5 11.5C2 8 1 6 1 4.5a4 4 0 0 1 8 0C9 6 8 8 5 11.5z" fill="#5b9591"/><circle cx="5" cy="4.5" r="1.5" fill="#fff"/></svg>
    <span>Wirkungskreis: Lindmar, Vehrholt, Ostenfeld, Kranau, Elbsdorf, Marlingen, Tessau</span>
  </div>
  <div class="field" style="top:3888px;height:33px">Name*</div>
  <div class="field" style="top:3930px;height:33px">Email*</div>
  <div class="field" style="top:3974px;height:56px;font-size:10px;padding-top:4px">Nachricht*</div>
  <div class="send">Absenden</div>
</section>

<footer class="footer">
  <svg class="abs" style="left:0;top:0" width="1200" height="222" viewBox="0 0 1200 222">
    <polygon points="0,11 1200,53 1200,222 0,222" fill="#4b4c4d"/>
    <polygon points="630,42 1200,22 1200,122" fill="#5b9591"/>
  </svg>
  <div class="footer-brand">Kersten Reden</div>
  <div class="footer-copy">© 2021 KerstenReden. Alle Rechte vorbehalten</div>
  <div class="footer-legal">Impressum / Datenschutz</div>
</footer>

</body>
</html>
```